Custom T Shirt Site Needs New Graphics for Homepage.

I am looking to have the homepage graphic redone. They need to unique images and give the site a fresh look. www.pennolark.com. I want new banners, New images for T Shirts, Polo Shirts, Sweatshirts, Hats, Jersey. I want the large banner on the homepage changed and the 3 banners to the right and below. I would look at a new layout of the homepage.

```html
<!DOCTYPE html>
<html lang="en">
<head>
<meta charset="utf-8">
<title>Pennolark – Custom T-Shirts</title>
<link rel="stylesheet" href="https://fonts.googleapis.com/css2?family=PT+Sans:wght@400;700&family=Arimo:wght@400;700&family=PT+Serif:ital@1&display=swap">
<style>
:root{
  --page-grey:#f4f4f4;
  --white:#ffffff;
  --navy:#1b4a7f;
  --heading-blue:#1d5a96;
  --text:#333333;
  --text-soft:#555555;
  --rule:#dcdcdc;
  --price-green:#5a9e2f;
  --accent-orange:#f39a1e;
  --banner-blue:#6aaee0;
  --banner-blue-mid:#4f97d2;
  --banner-blue-dark:#3a7fbd;
  --ornament:#b99a80;
}
*{margin:0;padding:0;box-sizing:border-box}
html,body{width:1052px;height:1200px;overflow:hidden}
body{position:relative;background:var(--white);font-family:"Arimo",Arial,sans-serif;color:var(--text)}
.abs{position:absolute}

.top-area{left:0;top:0;width:1052px;height:310px;background:var(--page-grey)}
.top-stripe{left:0;top:310px;width:1052px;height:14px;
  background:repeating-linear-gradient(90deg,#e9e9e9 0 2px,#f6f6f6 2px 4px)}
.footer-stripe{left:0;top:1188px;width:1052px;height:12px;
  background:repeating-linear-gradient(90deg,#e9e9e9 0 2px,#f6f6f6 2px 4px)}

.hero-banner{left:139px;top:0;width:775px;height:233px;border:1px solid #d7e08a;border-bottom:none;
  background:
    radial-gradient(ellipse 180px 120px at 120px 110px,rgba(20,30,50,.55),transparent 70%),
    radial-gradient(ellipse 110px 110px at 400px 120px,rgba(15,20,35,.6),transparent 70%),
    radial-gradient(ellipse 110px 120px at 670px 110px,rgba(15,20,35,.45),transparent 70%),
    radial-gradient(circle at 25% 20%,rgba(255,255,255,.25),transparent 40%),
    radial-gradient(circle at 80% 85%,rgba(255,255,255,.18),transparent 35%),
    linear-gradient(135deg,var(--banner-blue) 0%,var(--banner-blue-mid) 50%,var(--banner-blue-dark) 100%)}

.category-tabs{left:139px;top:232px;width:775px;height:52px;display:flex;
  box-shadow:0 6px 8px rgba(0,0,0,.12)}
.category-tab{flex:1;background:var(--white);border:1px solid #d5d5d5;border-left:none;display:flex;align-items:center;padding-left:6px}
.category-tab:first-child{border-left:1px solid #d5d5d5}
.tab-icon{width:34px;height:34px;border:1px solid #ddd;margin-right:6px;display:flex;align-items:center;justify-content:center}
.tab-icon span{width:22px;height:22px;border-radius:3px;display:block}
.tab-title{font-family:"PT Sans",sans-serif;font-size:13px;color:var(--navy);line-height:15px}
.tab-sub{font-size:8px;font-weight:700;color:var(--text-soft)}

.section-title{font-family:"PT Sans",sans-serif;font-weight:400;color:var(--heading-blue);font-size:24px;line-height:1}
.section-rule{height:1px;background:var(--rule)}
.title-badge{left:149px;top:348px;width:32px;height:32px;border-radius:50%;background:var(--accent-orange);border:2px solid #fbd59b}

.shirt{width:166px;height:170px;top:406px}
.shirt-red{left:157px;background:radial-gradient(ellipse 50% 50% at 50% 50%,#d81a26 0%,#c3131e 60%,rgba(195,19,30,0) 100%)}
.shirt-purple{left:336px;background:radial-gradient(ellipse 50% 50% at 50% 50%,#4f2590 0%,#421d7a 60%,rgba(66,29,122,0) 100%)}
.shirt-blue{left:515px;background:radial-gradient(ellipse 50% 50% at 50% 50%,#5a8fd2 0%,#4477bf 60%,rgba(68,119,191,0) 100%)}
.shirt-meta{top:586px;width:180px;text-align:center;font-weight:700;font-size:14px;line-height:19px;color:#444}
.shirt-meta .price-value{color:var(--price-green)}

.side-box{left:713px;width:193px;background:var(--white);border:1px solid #e1e1e1;box-shadow:0 2px 3px rgba(0,0,0,.1)}
.side-box-head{height:27px;background:var(--navy);color:var(--white);font-family:"PT Sans",sans-serif;font-size:16.5px;padding-left:11px;display:flex;align-items:center;gap:7px}
.side-item{padding:0 12px}
.side-item h4{font-size:10.5px;font-weight:700;color:var(--navy);letter-spacing:.4px}
.side-item p{font-family:"PT Serif",serif;font-style:italic;font-size:8.5px;color:var(--text-soft);margin-top:2px}
.ornament{height:1px;margin:7px 12px;background:linear-gradient(90deg,transparent,var(--ornament) 20%,var(--ornament) 80%,transparent);position:relative}
.ornament::after{content:"";position:absolute;left:50%;top:-2px;width:14px;height:5px;margin-left:-7px;border-top:1px solid #9a5a3a;border-bottom:1px solid #9a5a3a;background:var(--white)}

.product-list{list-style:none;font-size:11px;letter-spacing:.3px;color:var(--text);line-height:23.3px}
.btn-all{left:559px;top:883px;width:119px;height:23px;border-radius:4px;background:var(--navy);color:var(--white);font-size:12.5px;display:flex;align-items:center;justify-content:center}

.pricing-list{list-style:none;padding:8px 0 0 20px}
.pricing-list li{font-size:10.5px;font-weight:700;color:var(--navy);letter-spacing:.3px;line-height:19px;display:flex;align-items:center;gap:8px}

.cat-list{list-style:none;font-size:12px;line-height:23.4px;color:var(--text)}
.divider-v{left:485px;top:998px;width:1px;height:148px;background:var(--navy)}
.intro-text{left:533px;top:1010px;width:362px;font-size:11.2px;letter-spacing:.15px;line-height:18.8px;color:var(--text)}
.link{color:var(--navy);font-size:10.5px}
.link-underline{text-decoration:underline}
.link-bold{font-weight:700}
</style>
</head>
<body>
<div class="abs top-area"></div>
<div class="abs top-stripe"></div>

<div class="abs hero-banner" role="img" aria-label="Hand-drawn banner on textured blue: a brush-painted letter, a plus sign, a black t-shirt, an equals sign and a cheerful stick figure wearing a t-shirt with a heart"></div>

<nav class="abs category-tabs">
  <div class="category-tab"><div class="tab-icon" role="img" aria-label="Grey t-shirt"><span style="background:#9a9a9a"></span></div><div><div class="tab-title">T-Shirts</div><div class="tab-sub">Click here to see more</div></div></div>
  <div class="category-tab"><div class="tab-icon" role="img" aria-label="Orange polo shirt"><span style="background:#f07a3a"></span></div><div><div class="tab-title">Polo Shirts</div><div class="tab-sub">Click here to see more</div></div></div>
  <div class="category-tab"><div class="tab-icon" role="img" aria-label="Blue sweatshirt"><span style="background:#7f90b8"></span></div><div><div class="tab-title">Sweatshirts</div><div class="tab-sub">Click here to see more</div></div></div>
  <div class="category-tab"><div class="tab-icon" role="img" aria-label="Yellow cap"><span style="background:#f2b51c;border-radius:50%"></span></div><div><div class="tab-title">Hats &amp; Caps</div><div class="tab-sub">Click here to see more</div></div></div>
  <div class="category-tab"><div class="tab-icon" role="img" aria-label="White and navy jersey"><span style="background:linear-gradient(#1d2a55 35%,#f3f3f3 35%)"></span></div><div><div class="tab-title">Jerseys</div><div class="tab-sub">Click here to see more</div></div></div>
</nav>

<div class="abs title-badge"></div>
<h2 class="abs section-title" style="left:191px;top:351px">T-Shirts Styles</h2>
<div class="abs section-rule" style="left:149px;top:390px;width:757px"></div>

<div class="abs shirt shirt-red" role="img" aria-label="Red t-shirt product photo"></div>
<div class="abs shirt shirt-purple" role="img" aria-label="Purple t-shirt product photo"></div>
<div class="abs shirt shirt-blue" role="img" aria-label="Blue t-shirt product photo"></div>
<div class="abs shirt-meta" style="left:150px">Price: <span class="price-value">US $65</span><br>COD: AE001</div>
<div class="abs shirt-meta" style="left:328px">Price: <span class="price-value">US $65</span><br>COD: AE001</div>
<div class="abs shirt-meta" style="left:508px">Price: <span class="price-value">US $65</span><br>COD: AE001</div>

<aside class="abs side-box" style="top:401px;height:229px">
  <div class="side-box-head">Our Products</div>
  <div class="side-item" style="margin-top:12px"><h4>FREEE SHIPPING</h4><p>Order T-shirts Today...</p></div>
  <div class="ornament"></div>
  <div class="side-item"><h4>FREE 2-WEEK DELIVERY</h4><p>Guaranteed by Fri, Mar 21</p></div>
  <div class="ornament"></div>
  <div class="side-item"><h4>RUSH 1-WEEK DELIVERY</h4><p>Guaranteed by Sat, Mar 15</p></div>
  <div class="ornament"></div>
  <div class="side-item"><h4>NEED IT SOONER?</h4><p>Ask about Super Rush Delivery</p><p>View Daily Delivery Calendar</p></div>
</aside>

<h2 class="abs section-title" style="left:176px;top:700px">You Create</h2>
<ul class="abs product-list" style="left:180px;top:736px">
  <li>T Shirt</li><li>Cheap T-Shirts</li><li>Baby Clothing</li><li>Corporate Logo Apparel</li><li>Vinyl Banners</li><li>Cistom Unifoems</li>
</ul>
<ul class="abs product-list" style="left:360px;top:736px">
  <li>Sweatshirts</li><li>Womens Apparel</li><li>Hats</li><li>Family Reunions T-Shirts</li><li>Personalized Wedding Gifts</li><li>Jerseys</li>
</ul>
<ul class="abs product-list" style="left:562px;top:736px">
  <li>Polo Shirts</li><li>Teen Apparel</li><li>Bags</li><li>Custom Golf Apparel</li><li>Posters</li>
</ul>
<div class="abs btn-all">See All Products</div>

<aside class="abs side-box" style="top:704px;height:148px">
  <div class="side-box-head">
    <svg width="16" height="18" viewBox="0 0 16 18" aria-hidden="true"><path d="M8 1 L15 4 V9 C15 13 12 16 8 17 C4 16 1 13 1 9 V4 Z" fill="none" stroke="#fff" stroke-width="1.5"/><text x="8" y="13" font-size="9" text-anchor="middle" fill="#fff" font-family="Arial">$</text></svg>
    All-inclusive Pricing
  </div>
  <ul class="pricing-list">
    <li><svg width="9" height="9" viewBox="0 0 9 9" aria-hidden="true"><path d="M4.5 0 L9 4.5 L4.5 9 L0 4.5Z" fill="#1b4a7f"/></svg>No hidden fees</li>
    <li><svg width="9" height="9" viewBox="0 0 9 9" aria-hidden="true"><path d="M4.5 0 L9 4.5 L4.5 9 L0 4.5Z" fill="#1b4a7f"/></svg>No setup charges</li>
    <li><svg width="9" height="9" viewBox="0 0 9 9" aria-hidden="true"><path d="M4.5 0 L9 4.5 L4.5 9 L0 4.5Z" fill="#1b4a7f"/></svg>Free artist review</li>
  </ul>
  <div class="ornament"></div>
  <div class="side-item"><p>Learn How Pricing Works</p></div>
</aside>

<h2 class="abs section-title" style="left:176px;top:956px">Designs Ideas Categories</h2>
<div class="abs section-rule" style="left:149px;top:992px;width:749px"></div>
<ul class="abs cat-list" style="left:187px;top:1009px">
  <li>Sports (0)</li><li>Events (0)</li><li>Business (0)</li><li>Holiday (0)</li>
</ul>
<ul class="abs cat-list" style="left:373px;top:1009px">
  <li>School (0)</li><li>Religious (0)</li><li>Military (0)</li>
</ul>
<a class="abs link link-underline" style="left:309px;top:1095px">Most Popular Templates</a>
<div class="abs divider-v"></div>
<p class="abs intro-text">If you're running out of ideas about the style, design, layout and colors for your custom shirts, Pennolark has over 250 Design Ideas that you can use as a guide for your t-shirt creation. These design ideas were created by our very own team of in-house artists. You can modify the color, the style and the text on the shirt according to your preferences. You can start by browsing the design ideas categories on the left.</p>
<a class="abs link link-bold" style="left:533px;top:1142px">Read More...</a>

<div class="abs footer-stripe"></div>
</body>
</html>
```